my website is tavorinque.com. (brand name is ta belle vitrine) This is just a template that i have choose for. The content and the pictures are not about my business just the template.
I would like to have 4 pages for now. 1 homepage, which will be an overview for all pages, it is right now in this way. It will directly highlight my story. My website will tell an exclusive story about details which makes the difference and will make people happy with very small things. It will be art related but very stylish as well. I also want to have a event agenda on my homepage where people can see where my next event is. Page 2 my blog, where I will write weekly about mindset, lifestyle and details. Inspiration place for people who are looking for unique and exclusive approaches in life. Page 3 shop, where I will sell my stuff which is handmade and unique, it will be limited edition stuff. Mostly I will make the designs from marbling art, which I am a teacher for. (https://www.vidoranta.com/watch?v=KpwuzRaxTmo) check this video out for more. Page 4 is book page. Here people will be able to book private or group classes for marbling art (check the video). I have already a community of more than 500 people on gath rix, which will be my public as well. I wanna implement the gath rix button on this page as well. to be able to track.

This is about my website. I also need a logo for my brand, which will suit my website and my goals.

I can also give you a reference website, which really like as structure and style;
https://www.brightorvalco.com/products/the-morning-ledger?gclid=Xr4TpLmwq2HsVD9KEBsZTrc-WkPhyQ-uvlEjdRs3NKaOYFCBWMpuTzG8xyCVbhdnLWRqoaNf_2e8ZtpRvHbAwq9FLQ_hqgQ

Logo Text

ta belle vitrine

Coding

Coded - Design and coding required

Number of Pages Required

4 page

Requirements
Must have
• I can also give you a reference website, which really like as structure and style;
• https://www.brightorvalco.com/products/the-morning-ledger?gclid=Xr4TpLmwq2HsVD9KEBsZTrc-WkPhyQ-uvlEjdRs3NKaOYFCBWMpuTzG8xyCVbhdnLWRqoaNf_2e8ZtpRvHbAwq9FLQ_hqgQ

```html
<!DOCTYPE html>
<html lang="en">
<head>
<meta charset="utf-8">
<title>Ta Belle Vitrine</title>
<link rel="stylesheet" href="https://fonts.googleapis.com/css2?family=Roboto:wght@400;500;700&family=Open+Sans:ital,wght@0,400;0,600;1,400&display=swap">
<style>
:root{
  --ink:#333333;
  --text:#555555;
  --muted:#777777;
  --dark:#2b2b2b;
  --panel:#444444;
  --panel-mid:#6a6a6a;
  --band:#eeeeee;
  --line:#cccccc;
  --white:#ffffff;
  --black:#222222;
}
*{box-sizing:border-box;margin:0;padding:0}
html,body{width:1200px;height:3125px;overflow:hidden;background:var(--white)}
body{font-family:"Open Sans",Arial,sans-serif;color:var(--text);position:relative}
.abs{position:absolute}

/* header */
.site-header{position:absolute;left:0;top:0;width:1200px;height:115px;background:var(--white)}
.brand{left:100px;top:36px;display:flex;align-items:center;gap:14px}
.brand-mark{width:40px;height:40px;border:2px solid var(--ink);border-radius:50%}
.brand-name{font-family:"Roboto",sans-serif;font-size:23px;color:var(--ink);font-weight:400;line-height:1.1;width:130px}
.social-top{left:770px;top:18px;display:flex;gap:8px}
.social-top span{width:31px;height:31px;border-radius:50%;display:block}
.cart{left:958px;top:14px;display:flex;gap:14px;font-family:"Roboto",sans-serif}
.cart-title{font-size:15px;color:var(--ink)}
.cart-sub{font-size:12px;color:var(--muted);margin-top:4px}
.nav{top:78px;left:0;width:1200px;font-family:"Roboto",sans-serif;font-size:16px;color:var(--ink);font-weight:500}
.nav span{position:absolute;transform:translateX(-50%);white-space:nowrap}

/* hero */
.hero{position:absolute;left:0;top:115px;width:1200px;height:500px;background:linear-gradient(160deg,#4a3a34 0%,#6b4238 35%,#7a5048 55%,#3e3a3a 100%)}
.hero-shade{position:absolute;inset:0;background:rgba(0,0,0,.25)}
.hero h1{position:absolute;top:88px;width:100%;text-align:center;font-family:"Roboto",sans-serif;font-weight:700;font-size:58px;color:var(--white);letter-spacing:1px}
.hero p{position:absolute;top:172px;left:290px;width:620px;text-align:center;font-size:14px;line-height:25px;color:var(--white);font-weight:600}
.btn-outline{position:absolute;border:2px solid var(--white);color:var(--white);font-family:"Roboto",sans-serif;font-weight:500;border-radius:4px;text-align:center}
.hero .btn-outline{left:538px;top:257px;width:125px;height:50px;line-height:46px;font-size:16px}
.arrow{position:absolute;top:222px}

/* features */
.features{position:absolute;left:100px;top:567px;width:1000px;height:283px;display:flex;gap:3px}
.feature{flex:1;background:var(--panel);text-align:center;color:var(--white);box-shadow:0 10px 12px -6px rgba(0,0,0,.35);border-top:3px solid var(--white)}
.feature.mid{background:var(--panel-mid)}
.feature svg{margin-top:38px}
.feature h3{font-family:"Roboto",sans-serif;font-weight:500;font-size:21px;margin-top:18px}
.feature p{font-size:13px;line-height:22px;font-weight:600;margin:16px 34px 0}
.feature .btn-outline{position:static;display:inline-block;margin-top:22px;width:115px;height:42px;line-height:38px;font-size:13px;border-radius:8px}

/* about */
.section-title{position:absolute;width:1200px;text-align:center;font-family:"Roboto",sans-serif;font-weight:700;font-size:32px;color:var(--ink)}
.title-rule{position:absolute;left:560px;width:80px;height:2px;background:var(--ink)}
.about p{position:absolute;left:150px;width:900px;text-align:center;font-size:12.5px;line-height:22px;color:var(--text)}

/* products */
.products{position:absolute;left:0;top:1240px;width:1200px;height:500px;background:var(--band)}
.products h2{position:absolute;left:100px;top:50px;font-family:"Roboto",sans-serif;font-weight:700;font-size:26px;color:var(--ink)}
.products .rule{position:absolute;left:100px;top:106px;width:1000px;height:2px;background:var(--ink)}
.pager{position:absolute;top:52px;width:28px;height:26px;border:1px solid var(--ink);background:var(--white)}
.card{position:absolute;top:145px;width:232px;height:282px;background:var(--white);border:1px solid var(--line);border-radius:4px}
.card-img{margin:6px;height:150px;border-radius:4px}
.card h4{font-size:14px;font-weight:600;color:var(--ink);text-align:center;line-height:22px;margin:20px 14px 0}
.price{position:absolute;left:12px;bottom:12px;font-family:"Roboto",sans-serif;font-size:17px;color:var(--ink)}
.add{position:absolute;right:0;bottom:0;width:130px;height:36px;background:var(--panel);color:var(--white);font-family:"Roboto",sans-serif;font-size:14px;font-weight:500;line-height:36px;text-align:center;clip-path:polygon(12% 0,100% 0,100% 100%,0 100%)}

/* events */
.event{position:absolute;width:470px;height:100px}
.date{position:absolute;left:0;top:0;width:90px}
.date .m{height:46px;background:var(--panel-mid);color:var(--white);font-family:"Roboto",sans-serif;font-size:21px;font-weight:500;text-align:center;line-height:46px}
.date .d{height:46px;background:var(--black);color:var(--white);font-family:"Roboto",sans-serif;font-size:17px;text-align:center;line-height:46px}
.event h4{position:absolute;left:110px;top:-6px;font-family:"Roboto",sans-serif;font-size:22px;font-weight:500;color:var(--ink)}
.event .when{position:absolute;left:110px;top:28px;font-size:13px;color:var(--muted)}
.event p{position:absolute;left:110px;top:52px;width:362px;font-size:12.5px;line-height:22px;color:var(--text);text-align:justify}

/* testimonial */
.testimonial{position:absolute;left:0;top:2302px;width:1200px;height:421px;background:radial-gradient(ellipse at 50% 50%,#4a3e3a 0%,#2e2a29 60%,#1e1c1c 100%)}
.avatar{position:absolute;left:527px;top:75px;width:146px;height:146px;border-radius:50%;border:4px solid var(--white);background:linear-gradient(180deg,#c9a37c,#e6cbb0)}
.quote-mark{position:absolute;font-family:Georgia,serif;font-size:80px;color:var(--white);font-weight:700}
.testimonial p{position:absolute;left:230px;top:252px;width:740px;text-align:center;font-style:italic;font-size:16px;line-height:30px;color:var(--white)}
.testimonial .who{position:absolute;top:340px;width:100%;text-align:center;font-family:"Roboto",sans-serif;font-size:19px;font-weight:500;color:var(--white)}

/* footer */
.footer-brand{left:100px;top:2878px;display:flex;align-items:center;gap:14px}
.footer h5{position:absolute;font-family:"Roboto",sans-serif;font-weight:500;font-size:19px;color:var(--ink)}
.contact-item{position:absolute;left:383px;display:flex;gap:18px}
.contact-item .ic{width:36px;height:36px;border:2px solid var(--ink);border-radius:50%;display:flex;align-items:center;justify-content:center;flex:none}
.contact-item b{display:block;font-family:"Roboto",sans-serif;font-size:15px;font-weight:500;color:var(--ink)}
.contact-item span{display:block;font-size:12.5px;color:var(--ink);margin-top:4px}
.signup{position:absolute;left:696px;top:2837px;width:404px;height:42px;display:flex}
.signup .field{flex:1;border:1px solid var(--ink);font-size:13px;color:var(--muted);padding-left:12px;line-height:40px}
.signup .go{width:86px;background:var(--black);color:var(--white);font-family:"Roboto",sans-serif;font-weight:700;font-size:13px;text-align:center;line-height:42px}
.join{position:absolute;left:698px;top:2925px;font-family:"Roboto",sans-serif;font-size:15px;color:var(--ink);font-weight:500}
.social-foot{position:absolute;left:698px;top:2965px;display:flex;gap:12px}
.social-foot span{width:34px;height:34px;border:2px solid var(--ink);border-radius:50%;display:block}
.bottom-bar{position:absolute;left:0;top:3067px;width:1200px;height:58px;background:var(--black);color:var(--white);text-align:center;line-height:58px;font-family:"Open Sans",sans-serif;font-weight:600;font-size:14px}
</style>
</head>
<body>

<header class="site-header">
  <div class="abs brand"><span class="brand-mark"></span><span class="brand-name">ta belle vitrine</span></div>
  <div class="abs social-top">
    <span style="background:#3b5998"></span><span style="background:#34a4dc"></span><span style="background:#2a6a9e"></span><span style="background:#c8232c"></span>
  </div>
  <div class="abs cart">
    <svg width="34" height="32" viewBox="0 0 34 32"><path d="M6 10h22l-2 20H8z" fill="#222"/><path d="M11 10V7a6 6 0 0 1 12 0v3" stroke="#222" stroke-width="2.5" fill="none"/></svg>
    <div><div class="cart-title">Shopping Cart</div><div class="cart-sub">0 item(s) - $0.00</div></div>
  </div>
  <nav class="abs nav">
    <span style="left:545px">HOME</span><span style="left:677px">MY BLOG</span><span style="left:798px">SHOP</span><span style="left:910px">BOOK</span><span style="left:1052px">CONTACT US</span>
  </nav>
</header>

<section class="hero" role="img" aria-label="Marbling tray with swirled paints and jars of colour on a workbench">
  <div class="hero-shade"></div>
  <h1>TA BELLE VITRINE</h1>
  <p>Duis aute irure dolor in reprehenderit in voluptate velit esse cillum dolore eu fugiat nulla pariatur. Excepteur sint occaecat cupidatat non proident.</p>
  <div class="btn-outline">READ MORE</div>
  <svg class="arrow" style="left:22px" width="20" height="40" viewBox="0 0 20 40"><path d="M18 2L3 20l15 18" stroke="#fff" stroke-width="2" fill="none"/></svg>
  <svg class="arrow" style="left:1140px" width="20" height="40" viewBox="0 0 20 40"><path d="M2 2l15 18L2 38" stroke="#fff" stroke-width="2" fill="none"/></svg>
</section>

<section class="features">
  <div class="feature">
    <svg width="44" height="44" viewBox="0 0 44 44"><rect x="3" y="3" width="38" height="38" fill="none" stroke="#fff" stroke-width="3"/><path d="M22 6L38 22 22 38 6 22z" fill="none" stroke="#fff" stroke-width="3"/><rect x="17" y="17" width="10" height="10" fill="#fff"/></svg>
    <h3>DUIS AUTE IRURE DOLOR</h3>
    <p>Nemo enim ipsam voluptatem quia voluptas sit aspernatur aut odit aut fugit.</p>
    <span class="btn-outline">Read More</span>
  </div>
  <div class="feature mid">
    <svg width="44" height="44" viewBox="0 0 44 44"><rect x="3" y="3" width="38" height="38" fill="#fff"/><path d="M22 8L36 22H22z M22 36L8 22h14z" fill="#6a6a6a"/></svg>
    <h3>MARBLE ARTS</h3>
    <p>Nemo enim ipsam voluptatem quia voluptas sit aspernatur aut odit aut fugit.</p>
    <span class="btn-outline">Read More</span>
  </div>
  <div class="feature">
    <svg width="44" height="44" viewBox="0 0 44 44"><path d="M22 2L42 22 22 42 2 22z" fill="#fff"/><path d="M22 12L32 22 22 32 12 22z" fill="#444"/><rect x="19" y="19" width="6" height="6" fill="#fff"/></svg>
    <h3>AUTE IRURE DOLOR</h3>
    <p>Nemo enim ipsam voluptatem quia voluptas sit aspernatur aut odit aut fugit.</p>
    <span class="btn-outline">Read More</span>
  </div>
</section>

<section class="about">
  <h2 class="section-title" style="top:934px">ABOUT TA BELLE VITRINE</h2>
  <div class="title-rule" style="top:998px"></div>
  <p style="top:1040px">Nemo enim ipsam voluptatem quia voluptas sit aspernatur aut odit aut fugit, sed quia consequuntur magni dolores eos qui ratione voluptatem sequi nesciunt. Neque porro quisquam est, qui dolorem ipsum quia dolor sit amet, consectetur, adipisci velit, sed quia non numquam eius modi tempora incidunt ut labore et dolore magnam aliquam quaerat voluptatem.</p>
  <p style="top:1116px">Ut enim ad minima veniam, quis nostrum exercitationem ullam corporis suscipit laboriosam, nisi ut aliquid ex ea commodi consequatur? Quis autem vel eum iure reprehenderit qui in ea voluptate velit esse quam nihil molestiae consequatur.</p>
</section>

<section class="products">
  <h2>OUR PRODUCTS</h2>
  <div class="pager" style="left:1031px"><svg width="26" height="24" viewBox="0 0 26 24"><path d="M15 7l-5 5 5 5" stroke="#333" stroke-width="2" fill="none"/></svg></div>
  <div class="pager" style="left:1069px"><svg width="26" height="24" viewBox="0 0 26 24"><path d="M11 7l5 5-5 5" stroke="#333" stroke-width="2" fill="none"/></svg></div>
  <div class="rule"></div>
  <div class="card" style="left:100px"><div class="card-img" role="img" aria-label="Green and red marbled pattern in a tray" style="background:linear-gradient(135deg,#7bb48a,#c8d8a0 50%,#b85a4a)"></div><h4>Nemo enim ipsam voluptatem voluptas sit aspernatur</h4><span class="price">$37.00</span><span class="add">ADD TO CART</span></div>
  <div class="card" style="left:357px"><div class="card-img" role="img" aria-label="Dark marbling tray with drops of colour" style="background:linear-gradient(135deg,#4a4240,#2a2626 60%,#6b5a50)"></div><h4>Nemo enim ipsam voluptatem voluptas sit aspernatur</h4><span class="price">$37.00</span><span class="add">ADD TO CART</span></div>
  <div class="card" style="left:614px"><div class="card-img" role="img" aria-label="Purple and white marbled paper being lifted" style="background:linear-gradient(135deg,#7a4a6a,#c8b0c0 50%,#5a3848)"></div><h4>Nemo enim ipsam voluptatem voluptas sit aspernatur</h4><span class="price">$37.00</span><span class="add">ADD TO CART</span></div>
  <div class="card" style="left:871px"><div class="card-img" role="img" aria-label="Pink marbled pattern being combed by hand" style="background:linear-gradient(135deg,#a86a6a,#d8a8a0 50%,#8a5050)"></div><h4>Nemo enim ipsam voluptatem voluptas sit aspernatur</h4><span class="price">$37.00</span><span class="add">ADD TO CART</span></div>
</section>

<section class="events">
  <h2 class="section-title" style="top:1816px">OUR EVENTS</h2>
  <div class="title-rule" style="top:1880px"></div>
  <div class="event" style="left:100px;top:1940px"><div class="date"><div class="m">JUN</div><div class="d">15</div></div><h4>Nemo enim ipsam</h4><div class="when">June, 15 2017</div><p>Sed ut perspiciatis unde omnis iste natus error sit volup tatem accusantium doloremque laudantium totam rem aperiam, eaque ipsa quae abillo inventore.</p></div>
  <div class="event" style="left:636px;top:1940px"><div class="date"><div class="m">MAY</div><div class="d">15</div></div><h4>Nemo enim ipsam</h4><div class="when">May, 15 2017</div><p>Sed ut perspiciatis unde omnis iste natus error sit volup tatem accusantium doloremque laudantium totam rem aperiam, eaque ipsa quae abillo inventore.</p></div>
  <div class="event" style="left:100px;top:2103px"><div class="date"><div class="m">OCT</div><div class="d">20</div></div><h4>Nemo enim ipsam</h4><div class="when">Oct, 20 2017</div><p>Sed ut perspiciatis unde omnis iste natus error sit volup tatem accusantium doloremque laudantium totam rem aperiam, eaque ipsa quae abillo inventore.</p></div>
  <div class="event" style="left:636px;top:2103px"><div class="date"><div class="m">MAR</div><div class="d">09</div></div><h4>Nemo enim ipsam</h4><div class="when">Mar, 09 2017</div><p>Sed ut perspiciatis unde omnis iste natus error sit volup tatem accusantium doloremque laudantium totam rem aperiam, eaque ipsa quae abillo inventore.</p></div>
</section>

<section class="testimonial" role="img" aria-label="Dark marbled tray background behind a customer testimonial">
  <span class="quote-mark" style="left:430px;top:60px">&ldquo;</span>
  <div class="avatar" role="img" aria-label="Customer portrait photo"></div>
  <span class="quote-mark" style="left:712px;top:100px">&rdquo;</span>
  <p>Nemo enim ipsam voluptatem quia voluptas sit aspernatur aut odit aut fugit, sed quia consequuntur magni dolores eos qui ratione voluptatem sequi nesciunt.</p>
  <div class="who">- Maribel</div>
  <svg class="arrow" style="left:46px;top:190px" width="20" height="40" viewBox="0 0 20 40"><path d="M18 2L3 20l15 18" stroke="#fff" stroke-width="2" fill="none"/></svg>
  <svg class="arrow" style="left:1130px;top:190px" width="20" height="40" viewBox="0 0 20 40"><path d="M2 2l15 18L2 38" stroke="#fff" stroke-width="2" fill="none"/></svg>
</section>

<footer class="footer">
  <div class="abs footer-brand"><span class="brand-mark"></span><span class="brand-name">ta belle vitrine</span></div>
  <h5 style="left:383px;top:2786px">Contact Us</h5>
  <div class="contact-item" style="top:2842px"><span class="ic"><svg width="14" height="18" viewBox="0 0 14 18"><path d="M7 1a6 6 0 0 1 6 6c0 4-6 10-6 10S1 11 1 7a6 6 0 0 1 6-6z" fill="none" stroke="#333" stroke-width="1.8"/><circle cx="7" cy="7" r="2" fill="#333"/></svg></span><div><b>Address,</b><span>Harbour Row, Wellmere North</span></div></div>
  <div class="contact-item" style="top:2918px"><span class="ic"><svg width="10" height="16" viewBox="0 0 10 16"><rect x="1" y="1" width="8" height="14" rx="1.5" fill="none" stroke="#333" stroke-width="1.8"/><circle cx="5" cy="12" r="1" fill="#333"/></svg></span><div><b>PHONE:</b><span>180 555 0142</span></div></div>
  <div class="contact-item" style="top:2990px"><span class="ic"><svg width="16" height="12" viewBox="0 0 16 12"><rect x="1" y="1" width="14" height="10" fill="#333"/><path d="M1 1l7 6 7-6" stroke="#fff" stroke-width="1.4" fill="none"/></svg></span><div><b>EMAIL:</b><span>sales@tavorinque.com</span></div></div>
  <h5 style="left:698px;top:2790px">Sign up for special offers and style news:</h5>
  <div class="signup"><div class="field">Enter Your Email Address...</div><div class="go">SIGN UP</div></div>
  <div class="join">JOIN IN:</div>
  <div class="social-foot"><span></span><span></span><span></span><span></span><span></span><span></span><span></span><span></span></div>
  <div class="bottom-bar">Copyrights © 2017 Ta Belle Vitrine. All Rights Reserved</div>
</footer>

</body>
</html>
```